Wix Design for a Clothing Design Web Marketing Site

We need a Wix design and content (including any images and copy) for a clothing design web storefront, Sew To Suit (or sewtosuit). Rough ideas and content can be found at http://marenvoltis.wix.com/sewtosuit.

Sew To Suit is an innovative business concept that combines fashion and entertainment. The business model allows customers to actively participate in the creation of fashion designs/concepts , visualize the garment in the customer’s body in 3D, and buy the physical garment made specially to fit the customer.
The fashion consultant will be able to create the design based on client's desires and test various possibilities (size, fabric, cut, etc..) in front of the customer, using software Drapova (the software is a key component of this business model)
(when developing the website use images from Drapova)
After the design is created, the customer can choose to order the actual piece. The garment will be made according to the created design, the customer measurements.

Target Market(s)

Primarily women from 25 to 45, who are fashion enthusiasts and appreciate fit and exclusivity. They are hedonistic shoppers, who shop for entertainment.
Men (metrosexuals) who are fashion enthusiasts, also hedonistic shoppers.

Industry/Entity Type

Clothing

Font styles to use
Serif
Sans Serif

Requirements
Must have
• Must have a landing page (home) or section, that gives the consumer an idea of what Sew To Suit will do for them, an about page or section that tells about the company and product, a how it works page or section that describes how it works (http://marenvoltis.wix.com/sewtosuit#!services3/c192y), and page or section about pricing, and a page or section on how to contact us.
Nice to have
• Very modern and clean. The website must be based on the main picture of the studio in the example. If that studio is the store, what will the website look like?
• Colors yellow, grey and white. Use the zig zag in yellow and white. You can change the size of the lines. The zig zagi gives the modern and bold accent. Outfits in pictures must show nicely tailored garments.

```html
<!DOCTYPE html>
<html lang="en">
<head>
<meta charset="utf-8">
<title>Sew To Suit</title>
<link rel="stylesheet" href="https://fonts.googleapis.com/css2?family=Italiana&family=Josefin+Sans:wght@400;600&family=Open+Sans:wght@400;600&family=Roboto+Condensed:wght@400&family=Roboto+Slab:wght@300;400;700&display=swap">
<style>
:root{
  --yellow:#f3e53a;
  --yellow-soft:#f7ef9a;
  --white:#ffffff;
  --pink-white:#fbf3f3;
  --ink:#1e1e1e;
  --dark:#232323;
  --darker:#1a1a1a;
  --slate:#5a5d62;
  --nav:#5c6168;
  --card:#55585d;
  --frame:#6a6f76;
  --muted:#9a9a9a;
  --light:#e6e6e6;
}
*{margin:0;padding:0;box-sizing:border-box}
html,body{width:1021px;height:1200px;overflow:hidden;background:var(--darker)}
body{position:relative;font-family:"Open Sans",sans-serif}
.abs{position:absolute}

/* header */
.header{left:0;top:0;width:1021px;height:150px;background:var(--white)}
.header-dark{left:0;top:0}
.brand{left:88px;top:28px;display:flex;align-items:center;gap:12px}
.brand-dot{width:46px;height:46px;border-radius:50%;background:var(--yellow)}
.brand-name{font-family:"Roboto Slab",serif;font-weight:700;font-size:25px;color:var(--ink);letter-spacing:.5px}
.tagline{left:476px;top:30px;font-family:"Italiana",serif;font-size:40px;line-height:40px;color:var(--white)}

/* nav */
.nav{left:0;top:150px;width:1021px;height:34px;background:var(--nav);display:flex;padding-left:86px}
.nav a{font-family:"Roboto Condensed",sans-serif;font-size:14px;color:var(--white);text-decoration:none;line-height:34px;padding:0 24px}
.nav a.active{background:var(--dark);padding:0 20px}

/* hero */
.hero{left:0;top:184px;width:1021px;height:359px;background:var(--darker)}
.slider-frame{left:86px;top:217px;width:830px;height:291px;background:var(--frame)}
.slide-photo{left:93px;top:224px;width:816px;height:277px;background:linear-gradient(180deg,#f4f4f1 0%,#e9e6dc 45%,#d8d2c2 100%)}
.slide-photo::after{content:"";position:absolute;left:250px;top:0;width:170px;height:22px;background:var(--yellow-soft)}
.slide-title{left:115px;top:294px;font-family:"Josefin Sans",sans-serif;color:var(--ink);font-size:20px;line-height:25px;letter-spacing:.5px}
.slide-title .big{font-size:33px;line-height:38px}
.know-more{left:116px;top:409px;width:124px;height:36px;background:var(--ink);color:var(--yellow);font-family:"Roboto Condensed",sans-serif;font-size:14px;line-height:36px;text-align:center}
.arrow{top:332px}

/* content */
.side-pattern{top:543px;height:442px;background:linear-gradient(135deg,var(--yellow) 0%,var(--pink-white) 50%,var(--yellow) 100%)}
.panel{left:86px;top:543px;width:830px;height:452px;background:var(--white)}
.card{top:583px;width:129px;height:202px;background:var(--card);text-align:center;padding-top:58px}
.card h3{font-family:"Roboto Slab",serif;font-weight:300;font-size:15px;line-height:17px;color:var(--yellow);margin-bottom:19px;min-height:17px}
.card p{font-size:10.5px;line-height:14px;color:var(--white);padding:0 6px}
.card.two h3{margin-bottom:12px}
.icon{top:555px;width:70px;height:70px}

.feature{top:800px;width:400px;height:172px;background:var(--ink);padding:17px 140px 0 12px}
.feature h2{font-family:"Roboto Slab",serif;font-weight:300;font-size:18px;color:var(--yellow);margin-bottom:8px}
.feature p{font-size:10.5px;line-height:17px;color:var(--white);font-weight:600}
.feature a{display:inline-block;margin-top:4px;font-size:10.5px;font-weight:600;color:var(--yellow)}
.feature-photo{position:absolute;right:0;top:0;width:130px;height:172px;background:linear-gradient(180deg,var(--yellow) 0%,#efe03a 100%)}

/* footer */
.footer{left:0;top:985px;width:1021px;height:175px;background:var(--dark)}
.foot-col h4{font-family:"Roboto Condensed",sans-serif;font-weight:400;font-size:12.5px;color:var(--muted);margin-bottom:8px}
.foot-col li{list-style:none;font-size:10.5px;line-height:17px;color:var(--light)}
.foot-col .hl{color:var(--yellow)}
.email-field{width:201px;height:28px;background:var(--white);font-size:9px;color:var(--muted);padding:8px 8px}
.submit{margin-top:10px;width:80px;height:28px;background:var(--yellow);font-family:"Roboto Condensed",sans-serif;font-size:12px;color:var(--ink);text-align:center;line-height:28px}
.foot-brand{left:735px;top:1068px;display:flex;align-items:center;gap:8px}
.foot-brand .brand-dot{width:26px;height:26px;background:#8a8430}
.foot-brand .brand-name{font-size:15px;color:#8a8430}
.copyright{left:0;top:1160px;width:1021px;height:40px;background:#151515;color:var(--light);font-size:9.5px;text-align:center;line-height:40px}
</style>
</head>
<body>

<header class="abs header">
  <svg class="abs header-dark" width="1021" height="150" aria-hidden="true">
    <polygon points="470,0 1021,0 1021,150 406,150" fill="#222222"/>
  </svg>
  <div class="abs brand"><span class="brand-dot"></span><span class="brand-name">SEW TO SUIT</span></div>
  <p class="abs tagline">Clothes made specially for<br>You and designed by you</p>
</header>

<nav class="abs nav">
  <a class="active">Home</a>
  <a>What is Sew To Suit?</a>
  <a>How It Works?</a>
  <a>Price</a>
  <a>Contact Us</a>
</nav>

<section class="abs hero">
</section>
<div class="abs slider-frame"></div>
<div class="abs slide-photo" role="img" aria-label="Bright white design studio with curved yellow-lit consultation booths and computers"></div>
<h1 class="abs slide-title" style="font-weight:400">DESIGN YOUR OWN DRESS<br>&amp; SHOW YOUR CREATIVITY<br><span class="big">TO THE WORLD</span></h1>
<div class="abs know-more">KNOW MORE</div>
<svg class="abs arrow" style="left:22px" width="38" height="38" aria-label="Previous slide" role="img"><circle cx="19" cy="19" r="17" fill="none" stroke="#fff" stroke-width="2"/><polyline points="22,11 14,19 22,27" fill="none" stroke="#fff" stroke-width="2"/></svg>
<svg class="abs arrow" style="left:943px" width="38" height="38" aria-label="Next slide" role="img"><circle cx="19" cy="19" r="17" fill="none" stroke="#fff" stroke-width="2"/><polyline points="16,11 24,19 16,27" fill="none" stroke="#fff" stroke-width="2"/></svg>

<div class="abs side-pattern" style="left:0;width:86px" role="img" aria-label="Yellow and white zigzag pattern"></div>
<div class="abs side-pattern" style="left:916px;width:105px" role="img" aria-label="Yellow and white zigzag pattern"></div>
<main class="abs panel"></main>

<article class="abs card" style="left:94px"><h3>Be Inspired</h3><p>Be inspired by the latest trends, iconic styles from all eras and the most prestigious fashion shows</p></article>
<article class="abs card" style="left:231px"><h3>Design</h3><p>Learn about our unique process, where you become the designer</p></article>
<article class="abs card two" style="left:368px;padding-top:56px"><h3>Choose<br>The Fabric</h3><p>First rate fabrics &amp; highest quality materials</p></article>
<article class="abs card two" style="left:505px;padding-top:56px"><h3>See<br>Your Creation</h3><p>See youar creation<br>in 3D</p></article>
<article class="abs card" style="left:641px"><h3>Wear it</h3><p>Wear your design, fitted for your exact body measurements</p></article>
<article class="abs card two" style="left:778px;padding-top:56px"><h3>Have Fun,<br>Be creative</h3><p>First rate fabrics &amp; highest quality materials</p></article>

<svg class="abs icon" style="left:123px" viewBox="0 0 70 70" role="img" aria-label="Light bulb icon"><circle cx="35" cy="35" r="33" fill="#f3e53a" stroke="#fff" stroke-width="3"/><circle cx="35" cy="31" r="10" fill="none" stroke="#222" stroke-width="3"/><rect x="30" y="41" width="10" height="7" fill="#222"/></svg>
<svg class="abs icon" style="left:261px" viewBox="0 0 70 70" role="img" aria-label="Paint palette icon"><circle cx="35" cy="35" r="33" fill="#f3e53a" stroke="#fff" stroke-width="3"/><ellipse cx="34" cy="36" rx="15" ry="12" fill="#222"/><circle cx="28" cy="32" r="2.5" fill="#f3e53a"/><circle cx="36" cy="30" r="2.5" fill="#f3e53a"/><circle cx="40" cy="38" r="2.5" fill="#f3e53a"/></svg>
<svg class="abs icon" style="left:398px" viewBox="0 0 70 70" role="img" aria-label="Fabric and scissors icon"><circle cx="35" cy="35" r="33" fill="#f3e53a" stroke="#fff" stroke-width="3"/><path d="M18 32 H52 Q50 46 35 46 Q20 46 18 32 Z" fill="#222"/></svg>
<svg class="abs icon" style="left:534px" viewBox="0 0 70 70" role="img" aria-label="Dress icon"><circle cx="35" cy="35" r="33" fill="#f3e53a" stroke="#fff" stroke-width="3"/><path d="M30 18 H40 V30 L48 50 H22 L30 30 Z" fill="#222"/></svg>
<svg class="abs icon" style="left:670px" viewBox="0 0 70 70" role="img" aria-label="Top garment icon"><circle cx="35" cy="35" r="33" fill="#f3e53a" stroke="#fff" stroke-width="3"/><path d="M26 20 L44 20 L52 30 L46 34 V50 H24 V34 L18 30 Z" fill="#222"/></svg>
<svg class="abs icon" style="left:807px" viewBox="0 0 70 70" role="img" aria-label="Dancing couple icon"><circle cx="35" cy="35" r="33" fill="#f3e53a" stroke="#fff" stroke-width="3"/></svg>

<article class="abs feature" style="left:94px"><h2>Lorel ipsum dolor sit amet</h2><p>Donec pulvinar nec orci vel fermentum. Donec venenatis varius tincidunt. Aliquam erat volutpat. Maecenas rhoncus venenatis venenatis. Morbi aliquam nibh eget libero blandit, ac placerat tellus tristique.</p><a>Read More</a><div class="feature-photo" role="img" aria-label="Tailored black sheath dress on a yellow background"></div></article>
<article class="abs feature" style="left:507px"><h2>Lorel ipsum dolor sit amet</h2><p>Donec pulvinar nec orci vel fermentum. Donec venenatis varius tincidunt. Aliquam erat volutpat. Maecenas rhoncus venenatis venenatis. Morbi aliquam nibh eget libero blandit, ac placerat tellus tristique.</p><a>Read More</a><div class="feature-photo" role="img" aria-label="Navy tailored suit jacket on a mannequin, yellow background"></div></article>

<footer class="abs footer"></footer>
<div class="abs foot-col" style="left:115px;top:1026px"><h4>QUICK LINKS</h4><ul><li>Home</li><li>What is Sew To Suit?</li><li>How It Works?</li><li>Price</li><li>Contact Us</li></ul></div>
<div class="abs foot-col" style="left:280px;top:1026px"><h4>COMPANY INFO</h4><ul><li>58 Loom Street,</li><li>2nd Floor, Suite 9</li><li>Los Angeles, CA</li><li>USA</li><li>Ph: <span class="hl">555 0142 316</span></li><li>Email: <span class="hl">hello@sewtosuitstudio</span></li></ul></div>
<div class="abs foot-col" style="left:502px;top:1026px"><h4>SUBSCRIBE NEWSLETTER</h4><div class="email-field">Type your email id</div><div class="submit">SUBMIT</div></div>
<div class="abs foot-brand"><span class="brand-dot"></span><span class="brand-name">SEW TO SUIT</span></div>
<div class="abs copyright">© 2015, All Rights Reserved, Sew To Suit</div>

</body>
</html>
```